BrivoNest Learning App for Children with Dyslexia

Project Description:

We are seeking a talented UI/UX designer to create engaging and intuitive designs for Brivonest, an innovative educational app designed to help children learn letters and words through a multisensory learning approach. The app aims to be particularly helpful for children with dyslexia, providing a supportive and interactive learning environment.

Key App Features & Design Requirements:

Account Creation Screen: Design a welcoming and straightforward sign-up page that allows users to register with their email or continue with Quarnix. The design should be clean, focusing on user-friendliness and accessibility, adhering to our terms of service and privacy policy.

Main Screen Design: The main screen should allocate at least 4/6 of its height to the interactive drawing area. It needs to display word prompts in both correct and scrambled orders and include options to "Show all Words," "Play all words," and a search function. The interface should be vibrant, engaging, and easy to navigate for children.

Profile Section: Create a user-friendly profile page that allows users to edit their profile image, name, username, email, links, and bio. The design should be clean and encourage user engagement.

BrivoTally Page: This section will display the user's learning progress, including rankings, a learning curve, and recently learned words. It should visually represent progress in a motivating and understandable way, suitable for a younger audience.

Visual and Auditory Feedback Implementation: Incorporate elements that support visual and auditory feedback, using dyslexia-friendly formats. This includes choosing appropriate colors, fonts, and auditory cues.

Accessibility and Customization Settings: Designs should include settings for adjusting visual contrast, font size, and the word list to accommodate individual preferences and needs.

Feel free to add more interactions and/or pages.

Design preferences:

Color Scheme: Use a bright, inviting color palette that stimulates learning and engagement without overwhelming the users.
Font Selection: Opt for fonts that are readable and accessible, particularly for users with dyslexia.
Icons and Graphics: Design custom icons and graphics that are cohesive with the app's theme and purpose. Illustrations should be simple, relatable, and supportive of the learning process.

Target Market(s)

Educational

Industry/Entity Type

Educational

Colors
0054AA
0677BA
7BADD7
CADEEF
E8F1F8
0094D4
00A9DD
6FCCEA
C7EBF8
E9F6FB

Requirements
Must have
• Educational app, a writing area, scoring and account management
Nice to have
• Statistics, Ranking Page, Settings and some nice visual features

```html
<!DOCTYPE html>
<html lang="en">
<head>
<meta charset="utf-8">
<title>Brivonest – App Screens</title>
<link href="https://fonts.googleapis.com/css2?family=Montserrat:wght@400;500;600&family=Poppins:wght@400;500;600&family=Roboto:wght@500;700&display=swap" rel="stylesheet">
<style>
:root{
  --blue:#0054AA;
  --blue-mid:#0677BA;
  --blue-soft:#CADEEF;
  --blue-pale:#E8F1F8;
  --ink:#111111;
  --muted:#555555;
  --line:#9a9a9a;
  --canvas-grey:#DEDEDE;
  --white:#ffffff;
}
*{margin:0;padding:0;box-sizing:border-box}
html,body{width:1200px;height:807px;overflow:hidden;background:var(--white)}
.stage{position:absolute;left:0;top:0;width:1420px;height:955px;transform:scale(.8451);transform-origin:0 0}
.screen{position:absolute;top:25px;width:414px;height:896px;overflow:hidden;font-family:"Montserrat",sans-serif;color:var(--ink)}
.screen--signup{left:37px;background:var(--blue)}
.screen--main{left:497px;background:var(--white);box-shadow:0 2px 8px rgba(0,0,0,.12)}
.screen--profile{left:957px;background:var(--white);box-shadow:0 2px 8px rgba(0,0,0,.15)}
.abs{position:absolute}
.status{position:absolute;left:0;top:0;width:414px;height:34px;background:var(--blue);color:var(--white);font:600 12px "Roboto",sans-serif}
.status__time{position:absolute;left:12px;top:13px}
.status__icons{position:absolute;right:10px;top:10px}
.center{left:0;width:100%;text-align:center}
.home-bar{position:absolute;left:120px;top:876px;width:170px;height:2px;background:#111}

/* sign up */
.brand{top:92px;font:500 46px "Poppins",sans-serif;color:var(--white);letter-spacing:.5px}
.tagline{top:148px;font:400 18px "Poppins",sans-serif;color:var(--white)}
.card{left:26px;top:234px;width:357px;height:497px;background:var(--white);border-radius:8px}
.card__title{top:38px;font:700 22px "Roboto",sans-serif}
.card__sub{top:84px;font-size:14px;color:#222}
.field-line{left:23px;top:130px;width:313px;height:45px;border-bottom:2px solid var(--blue);font-size:14px;color:var(--muted);padding:11px 5px}
.btn{position:absolute;border-radius:24px;display:flex;align-items:center;justify-content:center;font:600 16px "Montserrat",sans-serif}
.btn--primary{background:var(--blue);color:var(--white)}
.btn--email{left:27px;top:204px;width:305px;height:46px}
.divider{left:11px;top:287px;width:336px;font-size:14px;color:#333;display:flex;align-items:center;gap:6px}
.divider::before,.divider::after{content:"";flex:1;height:1px;background:#444}
.btn--alt{left:27px;top:340px;width:305px;height:45px;background:var(--blue-soft);color:#222;gap:10px}
.btn--alt .dot{width:20px;height:20px;border-radius:50%;background:var(--blue)}
.legal{top:420px;font-size:14px;line-height:30px;color:#222}
.legal b{font-weight:600;color:#111}

/* main */
.menu{left:20px;top:63px}
.screen-title{top:63px;left:0;width:414px;text-align:center;font:500 22px "Roboto",sans-serif;padding-left:0}
.points{right:14px;top:66px;font:700 17px "Roboto",sans-serif}
.draw-area{left:7px;top:117px;width:400px;height:325px;background:var(--canvas-grey)}
.tool-btn{left:323px;top:361px;width:76px;height:70px;background:var(--blue);display:flex;align-items:center;justify-content:center}
.segmented{left:12px;top:466px;width:389px;height:51px;border:1.5px solid #444;border-radius:26px;font:700 15px "Roboto",sans-serif}
.segmented__item{position:absolute;top:2px;height:44px;display:flex;align-items:center;justify-content:center;border-radius:24px}
.segmented__item--off{left:2px;width:188px}
.segmented__item--on{left:190px;width:194px;background:var(--blue);color:var(--white)}
.word-tile{position:absolute;width:119px;height:101px;border-radius:16px;background:var(--white);box-shadow:0 1px 8px rgba(0,0,0,.16);display:flex;align-items:center;justify-content:center;text-align:center;font:600 25px/30px "Montserrat",sans-serif}
.word-tile--more{font-size:18px;letter-spacing:1px}
.btn--results{left:52px;top:798px;width:305px;height:46px}

/* profile */
.hero-photo{left:0;top:34px;width:414px;height:200px;background:linear-gradient(120deg,#6d8a6a 0%,#b9a58f 35%,#d8cbbb 60%,#a89a8a 100%)}
.sheet{left:0;top:166px;width:414px;height:760px;background:var(--white);border-radius:48px 48px 0 0}
.back{left:12px;top:70px;display:flex;align-items:center;gap:4px;font:500 10px "Roboto",sans-serif}
.avatar{left:136px;top:128px;width:142px;height:142px;border-radius:50%;border:2px solid var(--blue);background:linear-gradient(160deg,#a8785a,#6b4634 60%,#c9a8a6)}
.profile-title{top:274px;font:700 22px "Roboto",sans-serif}
.field{position:absolute;left:11px;width:388px;border:1px solid #555;border-radius:25px}
.field__label{position:absolute;left:28px;top:-13px;background:var(--white);padding:0 7px;font:500 17px "Montserrat",sans-serif;color:var(--blue)}
.field__value{position:absolute;left:29px;font-size:15px;color:#222}
.field__chev{position:absolute;right:22px;top:14px}
.links-list{position:absolute;left:29px;top:16px;font-size:15px;line-height:30px;color:#222}
.links-list .add{color:#888}
</style>
</head>
<body>
<div class="stage">

  <!-- Account creation -->
  <section class="screen screen--signup">
    <div class="status"><span class="status__time">9.45</span>
      <svg class="status__icons" width="74" height="16" viewBox="0 0 74 16" fill="#fff"><rect x="0" y="9" width="3" height="5"/><rect x="5" y="6" width="3" height="8"/><rect x="10" y="3" width="3" height="11"/><rect x="15" y="0" width="3" height="14"/><path d="M27 5a13 13 0 0 1 18 0l-2 2a10 10 0 0 0-14 0zM31 9a7 7 0 0 1 10 0l-2 2a4 4 0 0 0-6 0zM36 15l-2-2h4z"/><rect x="51" y="2" width="22" height="11" rx="2" fill="none" stroke="#fff" stroke-width="1.5"/><rect x="53" y="4" width="4" height="7"/></svg>
    </div>
    <div class="abs center brand">Brivonest</div>
    <div class="abs center tagline">Learn letters and words</div>
    <div class="abs card">
      <div class="abs center card__title">Create an Account</div>
      <div class="abs center card__sub">Enter your email to sign up for this app</div>
      <div class="abs field-line">Email@domain.com</div>
      <div class="btn btn--primary btn--email">Sign up with email</div>
      <div class="abs divider">Or Continue With</div>
      <div class="btn btn--alt"><span class="dot"></span>Quarnix</div>
      <div class="abs center legal">By clicking continue, you agree to our<br><b>Terms of Service</b> and <b>Privacy Policy</b></div>
    </div>
    <div class="home-bar"></div>
  </section>

  <!-- Main screen -->
  <section class="screen screen--main">
    <div class="status"><span class="status__time">9.45</span>
      <svg class="status__icons" width="74" height="16" viewBox="0 0 74 16" fill="#fff"><rect x="0" y="9" width="3" height="5"/><rect x="5" y="6" width="3" height="8"/><rect x="10" y="3" width="3" height="11"/><rect x="15" y="0" width="3" height="14"/><path d="M27 5a13 13 0 0 1 18 0l-2 2a10 10 0 0 0-14 0zM31 9a7 7 0 0 1 10 0l-2 2a4 4 0 0 0-6 0zM36 15l-2-2h4z"/><rect x="51" y="2" width="22" height="11" rx="2" fill="none" stroke="#fff" stroke-width="1.5"/><rect x="53" y="4" width="4" height="7"/></svg>
    </div>
    <svg class="abs menu" width="37" height="32" viewBox="0 0 37 32"><g stroke="#0054AA" stroke-width="3.5" stroke-linecap="round"><line x1="2" y1="3" x2="35" y2="3"/><line x1="2" y1="16" x2="35" y2="16"/><line x1="2" y1="29" x2="35" y2="29"/></g></svg>
    <div class="abs screen-title">Main Screen</div>
    <div class="abs points">16 Points</div>
    <div class="abs draw-area"></div>
    <div class="abs tool-btn">
      <svg width="48" height="50" viewBox="0 0 48 50"><path d="M22 4C10 4 3 13 3 24s8 21 19 21c5 0 6-3 4-6s0-6 4-6h5c4 0 7-3 7-8C42 13 33 4 22 4z" fill="#fff"/><g fill="#0054AA"><circle cx="14" cy="17" r="3.5"/><circle cx="11" cy="28" r="3.5"/><circle cx="24" cy="13" r="3.5"/><circle cx="18" cy="37" r="3.5"/></g><rect x="42" y="10" width="3" height="34" rx="1.5" fill="#fff"/><rect x="41.5" y="4" width="4" height="7" rx="2" fill="#fff"/></svg>
    </div>
    <div class="abs segmented">
      <div class="segmented__item segmented__item--off">Show All Words</div>
      <div class="segmented__item segmented__item--on">Play All Words</div>
    </div>
    <div class="word-tile" style="left:19px;top:540px">Word<br>1</div>
    <div class="word-tile" style="left:147px;top:540px">Word<br>2</div>
    <div class="word-tile" style="left:276px;top:540px">Word<br>3</div>
    <div class="word-tile" style="left:19px;top:663px">Word<br>4</div>
    <div class="word-tile" style="left:147px;top:663px">Word<br>5</div>
    <div class="word-tile word-tile--more" style="left:276px;top:663px">••••</div>
    <div class="btn btn--primary btn--results">Show Me The Results</div>
    <div class="home-bar"></div>
  </section>

  <!-- Profile -->
  <section class="screen screen--profile">
    <div class="status"><span class="status__time">9.45</span>
      <svg class="status__icons" width="74" height="16" viewBox="0 0 74 16" fill="#fff"><rect x="0" y="9" width="3" height="5"/><rect x="5" y="6" width="3" height="8"/><rect x="10" y="3" width="3" height="11"/><rect x="15" y="0" width="3" height="14"/><path d="M27 5a13 13 0 0 1 18 0l-2 2a10 10 0 0 0-14 0zM31 9a7 7 0 0 1 10 0l-2 2a4 4 0 0 0-6 0zM36 15l-2-2h4z"/><rect x="51" y="2" width="22" height="11" rx="2" fill="none" stroke="#fff" stroke-width="1.5"/><rect x="53" y="4" width="4" height="7"/></svg>
    </div>
    <div class="abs hero-photo" role="img" aria-label="Header photo of children learning in a classroom"></div>
    <div class="abs sheet"></div>
    <div class="abs back"><svg width="14" height="22" viewBox="0 0 14 22"><path d="M11 2 3 11l8 9" fill="none" stroke="#111" stroke-width="2.5" stroke-linecap="round"/></svg>Back</div>
    <div class="abs avatar" role="img" aria-label="Profile photo of the child user"></div>
    <div class="abs center profile-title">Edit Profile Image</div>

    <div class="field" style="top:341px;height:51px"><span class="field__label">Name</span><span class="field__value" style="top:14px">Mara Delling</span>
      <svg class="field__chev" width="12" height="22" viewBox="0 0 12 22"><path d="M2 2l8 9-8 9" fill="none" stroke="#333" stroke-width="2"/></svg></div>
    <div class="field" style="top:429px;height:51px"><span class="field__label">Username</span><span class="field__value" style="top:14px">@username</span>
      <svg class="field__chev" width="12" height="22" viewBox="0 0 12 22"><path d="M2 2l8 9-8 9" fill="none" stroke="#333" stroke-width="2"/></svg></div>
    <div class="field" style="top:517px;height:51px"><span class="field__label">Email</span><span class="field__value" style="top:14px">name@domain.com</span>
      <svg class="field__chev" width="12" height="22" viewBox="0 0 12 22"><path d="M2 2l8 9-8 9" fill="none" stroke="#333" stroke-width="2"/></svg></div>
    <div class="field" style="top:604px;height:143px;border-radius:20px"><span class="field__label">Links</span>
      <div class="links-list">website.net<br>mylink.net<br>yourlink.net<br><span class="add">+ Add link</span></div></div>
    <div class="field" style="top:787px;height:51px"><span class="field__label">Bio</span><span class="field__value" style="top:14px">A description of this user.</span>
      <svg class="field__chev" width="12" height="22" viewBox="0 0 12 22"><path d="M2 2l8 9-8 9" fill="none" stroke="#333" stroke-width="2"/></svg></div>
    <div class="home-bar"></div>
  </section>

</div>
</body>
</html>
```